Pull Up Banner - Recruitment Company

We would like a design for a pull up banner.

For context: we are a recruitment business. We specialise in helping people in healthcare industry to find jobs in Australia.

I have come up with several ideas and text for the banner. Feel free to use the following as you see appropriate:

- Our logo (see attached)
- 'Healthcare Recruitment Agency'
- Some sort of imagine / cartoon of medical professionals (ie. doctor, nurse, physiotherapist, speech pathologist). A cartoon is more friendly than committing to a photo
- 'Empowering your next career move'
- 'Discover tailored opportunities based on your career preferences'
- Dot points (allied health, nursing, medical imaging)
- Contact info at the bottom including our website (www.quellastaffing.com.au, our Instagram handle @quellastaffing, Mobile: XXXX XXX XXX. The title section for contact information could be 'Get in touch:'

Feel free to submit a couple of designs and we can merge aspects that look good on your designs and find the perfect fit.
Thank you
Updates

Hello,

Thank you for your initial submissions to this project. I appreciate the time you've invested.

After reviewing the first attempt, I'd like to share some feedback and initial observations:

- Professionalism and engagement: Is the overall appearance of the banner professional? It's crucial that we have a high-quality design as this will represent our business.

- Image selection: The image (whether cartoon or real people) appears quite generic. Please consider submitting the banner with a few different photos in the middle for us to choose from. Ensure the image is a good fit and not simply a generic stock photo.

- Contact section: Kindly remove the phone number; we no longer wish to include it on the banner. Instead, please include our website (www.quellastaffing.com.au) and Instagram handle (@quellastaffing).

- Color scheme: White, black, and red/pink are preferred, or alternatively, blue. However, please avoid incorporating too many different colors as it may detract from the professional appearance.

We will be printing the design on a banner and require it to look professional and engaging.

Thank you once again for your submissions. I hope the feedback provided above is helpful.

Warm regards,

Target Market(s)

Allied Health Australia

Font styles to use
Serif

Colors
0054AA
0677BA
7BADD7
CADEEF
E8F1F8
0094D4
00A9DD
6FCCEA
C7EBF8
E9F6FB
EB3D1F
EC4F4E
F09395
F8D3D4
FCEDEE

```html
<!DOCTYPE html>
<html lang="en">
<head>
<meta charset="utf-8">
<title>Quella Staffing – Healthcare Recruitment Pull Up Banner</title>
<link rel="stylesheet" href="https://fonts.googleapis.com/css2?family=League+Spartan:wght@600;700;800&family=Jost:wght@400;500&family=Poppins:wght@500;600;700&display=swap">
<style>
  :root {
    --navy: #0a1587;
    --navy-deep: #0b0f5a;
    --royal: #3442d8;
    --sky: #7aa6f5;
    --white: #ffffff;
    --ink: #2a2a2e;
    --icon: #1f2fd0;
    --divider: #e3e3ea;
    --art-pink: #d98ad8;
    --art-lilac: #f1d7f2;
  }
  * { margin: 0; padding: 0; box-sizing: border-box; }
  html, body { width: 1200px; height: 2400px; overflow: hidden; background: var(--white); }
  .banner { position: relative; width: 1200px; height: 2400px; overflow: hidden; background: var(--navy); }
  .backdrop { position: absolute; inset: 0; width: 1200px; height: 2400px; }

  .brand {
    position: absolute; top: 150px; left: 0; width: 1200px; text-align: center;
    font-family: "League Spartan", sans-serif; font-weight: 700; font-size: 82px;
    letter-spacing: 6px; color: var(--white);
  }

  .headline { position: absolute; top: 330px; left: 0; width: 1200px; text-align: center;
    font-family: "League Spartan", sans-serif; font-weight: 800; line-height: 0.82; }
  .headline__lead { display: block; font-size: 118px; color: var(--sky); letter-spacing: -1px; }
  .headline__main { display: block; font-size: 138px; color: var(--white); letter-spacing: -2px; margin-top: 6px; }

  .hero-art {
    position: absolute; left: 120px; top: 700px; width: 980px; height: 880px;
    border-radius: 50%;
    background: radial-gradient(ellipse at center, rgba(241,215,242,0.85) 0%, rgba(217,138,216,0.55) 45%, rgba(217,138,216,0) 72%);
  }

  .tagline { position: absolute; top: 1630px; left: 0; width: 1200px; text-align: center; color: var(--ink); }
  .tagline__light { display: block; font-family: "Jost", sans-serif; font-weight: 400; font-size: 84px; letter-spacing: -2px; line-height: 1; }
  .tagline__bold { display: block; font-family: "League Spartan", sans-serif; font-weight: 800; font-size: 88px; letter-spacing: -1px; line-height: 1; margin-top: 10px; }
  .tagline__sub { display: block; font-family: "Poppins", sans-serif; font-weight: 600; font-size: 48px; letter-spacing: -1px; margin-top: 22px; }

  .specialties { position: absolute; top: 1935px; left: 60px; width: 1080px; height: 135px; }
  .specialty { position: absolute; top: 0; width: 340px; margin-left: -170px; text-align: center;
    font-family: "Poppins", sans-serif; font-weight: 500; font-size: 34px; color: var(--ink); }
  .specialty svg { display: block; margin: 0 auto 14px; width: 64px; height: 64px; }
  .specialty--allied { left: 180px; }
  .specialty--nursing { left: 502px; }
  .specialty--imaging { left: 868px; }
  .specialties__divider { position: absolute; top: 0; width: 2px; height: 135px; background: var(--divider); }

  .contact-title { position: absolute; top: 2116px; left: 0; width: 1200px; text-align: center;
    font-family: "Poppins", sans-serif; font-weight: 700; font-size: 46px; letter-spacing: 7px; color: var(--ink); }
  .contact-url { position: absolute; top: 2185px; left: 107px; width: 966px; height: 82px; border-radius: 41px;
    background: var(--navy); color: var(--white); text-align: center; line-height: 84px;
    font-family: "Poppins", sans-serif; font-weight: 700; font-size: 44px; letter-spacing: 3px; }
  .social { position: absolute; top: 2290px; left: 0; width: 1200px; display: flex; justify-content: center; gap: 22px; }
  .social__dot { width: 50px; height: 50px; border-radius: 50%; background: var(--royal); }
</style>
</head>
<body>
<main class="banner">
  <svg class="backdrop" viewBox="0 0 950 2205" preserveAspectRatio="none" aria-hidden="true">
    <rect width="950" height="2205" fill="var(--navy)"/>
    <polygon points="0,590 430,780 0,995" fill="var(--navy-deep)"/>
    <polygon points="0,995 950,570 950,1085 0,1510" fill="var(--royal)"/>
    <polygon points="950,1085 950,1445 600,1300" fill="var(--navy-deep)"/>
    <polygon points="0,1510 470,1295 950,1445 950,2205 0,2205" fill="var(--white)"/>
  </svg>

  <div class="brand">QUELLA STAFFING</div>

  <h1 class="headline">
    <span class="headline__lead">HEALTHCARE</span>
    <span class="headline__main">RECRUITMENT</span>
    <span class="headline__main">AGENCY</span>
  </h1>

  <div class="hero-art" role="img" aria-label="Illustration of a physiotherapist treating a patient's knee in a clinic room with a wheelchair, exercise ball, plant and X-ray display"></div>

  <p class="tagline">
    <span class="tagline__light">EMPOWER YOUR</span>
    <span class="tagline__bold">NEXT CAREER MOVE</span>
    <span class="tagline__sub">Tailored opportunities that fit you</span>
  </p>

  <section class="specialties">
    <div class="specialty specialty--allied">
      <svg viewBox="0 0 64 64" aria-hidden="true"><path d="M32 54 L10 32 A12 12 0 0 1 32 16 A12 12 0 0 1 54 32 Z" fill="var(--icon)"/></svg>
      Allied Health
    </div>
    <span class="specialties__divider" style="left:372px"></span>
    <div class="specialty specialty--nursing">
      <svg viewBox="0 0 64 64" aria-hidden="true"><rect x="24" y="8" width="16" height="48" rx="3" fill="var(--icon)"/><rect x="8" y="24" width="48" height="16" rx="3" fill="var(--icon)"/></svg>
      Nursing
    </div>
    <span class="specialties__divider" style="left:637px"></span>
    <div class="specialty specialty--imaging">
      <svg viewBox="0 0 64 64" aria-hidden="true"><circle cx="26" cy="28" r="18" fill="none" stroke="var(--icon)" stroke-width="7"/><rect x="14" y="30" width="44" height="8" rx="2" fill="var(--ink)"/><rect x="46" y="38" width="5" height="16" fill="var(--ink)"/></svg>
      Medical Imaging
    </div>
  </section>

  <h2 class="contact-title">GET IN TOUCH</h2>
  <div class="contact-url">www.quellastaffing.com.au</div>
  <div class="social" aria-hidden="true">
    <span class="social__dot"></span>
    <span class="social__dot"></span>
    <span class="social__dot"></span>
  </div>
</main>
</body>
</html>
```